MRT Property - Business Cards

Looking for a business card & general letterhead, signage etc design for our new logo.

Colours:
000a20
0056a2
00b5ef
0088ce
68cef2

Fonts:
Poppins
Karla

Please keep look and feel of new brand - example in the zip package I sent.

```html
<!DOCTYPE html>
<html lang="en">
<head>
<meta charset="utf-8">
<title>MRT Property – Business Cards</title>
<link href="https://fonts.googleapis.com/css2?family=Poppins:wght@400;500;600;700&family=Karla:wght@400;500&display=swap" rel="stylesheet">
<style>
  :root{
    --ink:#000a20;
    --navy-card:#161c36;
    --blue-deep:#0056a2;
    --blue-mid:#0088ce;
    --blue-bright:#00b5ef;
    --blue-soft:#68cef2;
    --paper:#f7f7f8;
    --text:#2a2d36;
    --stage:#1c1c1e;
  }
  *{margin:0;padding:0;box-sizing:border-box}
  html,body{width:1200px;height:852px;overflow:hidden;background:var(--stage)}
  .sheet{position:relative;width:1200px;height:852px}
  .card{position:absolute;top:270px;width:520px;height:300px;border-radius:18px;overflow:hidden;box-shadow:0 14px 30px rgba(0,0,0,.45)}
  .card--back{left:50px;background:linear-gradient(135deg,#1d2442,var(--navy-card) 60%,#10152b)}
  .card--front{left:630px;background:var(--paper)}
  .wordmark{font-family:"Poppins",sans-serif;font-weight:700;color:var(--blue-deep);display:flex;align-items:center;gap:10px;white-space:nowrap;letter-spacing:.5px}
  .wordmark__dot{width:14px;height:14px;background:var(--blue-bright);display:inline-block}
  .card--back .wordmark{position:absolute;left:86px;top:112px;font-size:40px}
  .back__url{position:absolute;right:34px;bottom:40px;font-family:"Karla",sans-serif;font-size:12px;letter-spacing:5px;color:#c9cfdc}
  .back__rule{position:absolute;left:0;right:0;bottom:18px;height:4px;background:linear-gradient(90deg,var(--blue-deep),var(--blue-mid) 55%,var(--blue-bright))}
  .card--front .wordmark{position:absolute;left:28px;top:40px;font-size:30px}
  .portrait{position:absolute;right:26px;top:18px;width:210px;height:140px;background:radial-gradient(circle at 35% 35%,#d9b49e 0 18%,transparent 19%),linear-gradient(180deg,#eef0f2 0 45%,#1f2a48 46%,#1a2340);}
  .front__curve{position:absolute;left:0;top:0;width:520px;height:300px}
  .name{position:absolute;left:28px;top:164px;font-family:"Poppins",sans-serif;font-weight:600;font-size:20px;color:var(--blue-mid)}
  .name-rule{position:absolute;left:28px;top:200px;width:170px;height:1.5px;background:var(--blue-mid)}
  .contacts{position:absolute;left:28px;top:214px;list-style:none;font-family:"Poppins",sans-serif;font-size:12.5px;color:var(--text)}
  .contacts li{display:flex;align-items:center;gap:10px;height:20px}
  .contacts svg{width:12px;height:12px;fill:var(--blue-deep)}
  .address{position:absolute;right:28px;top:168px;font-family:"Poppins",sans-serif;font-size:12px;color:var(--text)}
</style>
</head>
<body>
<main class="sheet">
  <section class="card card--back" aria-label="Card back">
    <div class="wordmark"><span class="wordmark__dot"></span>MRT Property</div>
    <p class="back__url">www.mrtproperty.com</p>
    <div class="back__rule"></div>
  </section>

  <section class="card card--front" aria-label="Card front">
    <div class="portrait" role="img" aria-label="Portrait photo of the agent"></div>
    <svg class="front__curve" viewBox="0 0 520 300" aria-hidden="true">
      <path d="M0 158 H230 C262 158 262 158 290 158 H520" fill="none" stroke="var(--paper)" stroke-width="0"/>
      <path d="M130 300 L284 158 H520" fill="none" stroke="none"/>
      <path d="M28 205 C120 205 180 172 236 162 C250 159 262 158 284 158 H494" fill="none" stroke="var(--blue-mid)" stroke-width="1.3"/>
    </svg>
    <div class="wordmark"><span class="wordmark__dot"></span>MRT Property</div>
    <h1 class="name">Callum Reid</h1>
    <div class="name-rule"></div>
    <ul class="contacts">
      <li><svg viewBox="0 0 24 24"><path d="M6.6 10.8a15 15 0 0 0 6.6 6.6l2.2-2.2c.3-.3.7-.4 1-.2 1.1.4 2.3.6 3.6.6.6 0 1 .4 1 1V20c0 .6-.4 1-1 1A17 17 0 0 1 3 4c0-.6.4-1 1-1h3.5c.6 0 1 .4 1 1 0 1.3.2 2.5.6 3.6.1.3 0 .7-.2 1z"/></svg>555-010-2020</li>
      <li><svg viewBox="0 0 24 24"><path d="M2 5h20v14H2zm2 2v.5l8 5 8-5V7l-8 5z"/></svg>callum@mrtproperty.com</li>
      <li><svg viewBox="0 0 24 24"><path d="M12 2a10 10 0 1 0 0 20 10 10 0 0 0 0-20zm6.9 6h-3a15 15 0 0 0-1.3-3.9A8 8 0 0 1 18.9 8zM12 4c.8 1.2 1.5 2.5 1.9 4h-3.8c.4-1.5 1.1-2.8 1.9-4zM4.3 14a8 8 0 0 1 0-4h3.4a17 17 0 0 0 0 4zm.8 2h3a15 15 0 0 0 1.3 3.9A8 8 0 0 1 5.1 16zm3-8h-3a8 8 0 0 1 4.3-3.9C8.8 5.3 8.4 6.6 8.1 8zM12 20c-.8-1.2-1.5-2.5-1.9-4h3.8c-.4 1.5-1.1 2.8-1.9 4zm2.3-6H9.7a15 15 0 0 1 0-4h4.6a15 15 0 0 1 0 4zm.3 5.9c.6-1.2 1-2.5 1.3-3.9h3a8 8 0 0 1-4.3 3.9zM16.3 14a17 17 0 0 0 0-4h3.4a8 8 0 0 1 0 4z"/></svg>www.mrtproperty.com</li>
    </ul>
    <p class="address">52 Harbour Line Road Westmead</p>
  </section>
</main>
</body>
</html>
```